Dental Practice Website design

Design a new website for Brambleford Dental Practice.
Design should be warm, neutral in colour, with some small amount of bright colour if needed but kept to a minimum. Website should look professional, high end. Home page should be easy to navigate and simple for patients to be able to book online.
Logo in files along with some examples of websites that we like. Please ask if any further info needed.
Menu should have:
About
New Patients
Treatments
Fees
Contact Us

Industry/Entity Type

Dentistry

Number of Pages Required

4 page

Font styles to use
Sans Serif

Colors

Designer to choose colors to be used in the design.

Requirements
Must have
• Ravelle ratings badge, book online button,
Nice to have
• neutral, relaxing colours
Should not have
• harsh, bright colours!

```html
<!DOCTYPE html>
<html lang="en">
<head>
<meta charset="utf-8">
<title>Brambleford Dental Practice</title>
<link href="https://fonts.googleapis.com/css2?family=Lato:wght@300;400;700;900&family=Outfit:wght@300;400;600;700;800&display=swap" rel="stylesheet">
<style>
:root{
  --gold:#d9a35e;
  --gold-dark:#c98f45;
  --ink:#1b2d33;
  --text:#5f6569;
  --light:#f3f3f3;
  --footer:#1d3035;
  --white:#ffffff;
}
*{box-sizing:border-box;margin:0;padding:0}
html,body{width:1200px;height:3813px;overflow:hidden}
body{position:relative;background:var(--white);font-family:"Lato",sans-serif;color:var(--text)}
.abs{position:absolute}
.btn{position:absolute;display:flex;align-items:center;justify-content:center;border:3px solid var(--gold);border-radius:6px;font-family:"Lato",sans-serif;font-weight:700;font-size:15px;color:var(--ink);background:var(--white);letter-spacing:.3px}
.h2{font-family:"Outfit",sans-serif;font-weight:400;font-size:42px;color:var(--ink);line-height:1.05;letter-spacing:-.5px}
.h2 b{font-weight:800}
.rule{position:absolute;height:4px;width:52px;background:var(--gold)}
.para{position:absolute;font-size:16px;line-height:25px;color:var(--text)}
.photo{position:absolute;border-radius:36px;overflow:hidden}

/* header */
.topbar{position:absolute;left:259px;top:0;width:941px;height:41px;background:var(--gold);clip-path:polygon(0 0,100% 0,100% 100%,28px 100%)}
.topbar .dots{position:absolute;left:66px;top:14px;display:flex;gap:16px}
.topbar .dots span{width:13px;height:13px;border-radius:50%;background:var(--white)}
.topbar .info{position:absolute;top:10px;font-size:15px;color:var(--white);display:flex;align-items:center;gap:7px}
.topbar .info b{font-weight:900;font-size:13px}
.logo{position:absolute;left:100px;top:12px;width:144px;height:99px;color:#6d7377;font-family:"Lato",sans-serif;font-weight:300;text-align:center}
.logo .mark{width:14px;height:14px;border:1px solid #6d7377;margin:4px auto 8px}
.logo .name{font-size:20px;letter-spacing:.5px;line-height:1.1}
.logo .sub{font-size:12px;letter-spacing:1px;margin-top:4px}
.nav{position:absolute;left:294px;top:74px;display:flex;gap:32px;font-size:15px;font-weight:700;color:#5c6266;letter-spacing:.3px}
.nav .active{color:var(--gold)}

/* hero */
.hero{position:absolute;left:0;top:123px;width:1200px;height:559px;background:linear-gradient(90deg,#f1f1f0 0%,#e9e8e6 38%,#c9cbcd 55%,#b9c9d4 75%,#8fb5cf 100%)}
.hero .welcome{position:absolute;left:104px;top:130px;font-family:"Outfit",sans-serif;font-weight:300;font-size:33px;color:var(--ink)}
.hero .big{position:absolute;left:101px;top:172px;font-family:"Outfit",sans-serif;font-weight:800;font-size:76px;color:var(--ink);letter-spacing:-1px;line-height:1}
.hero .sub{position:absolute;left:104px;top:270px;font-family:"Outfit",sans-serif;font-weight:300;font-size:42px;color:var(--ink)}
.hero .dots{position:absolute;left:48px;top:218px;display:flex;flex-direction:column;gap:8px}
.hero .dots span{width:7px;height:7px;border-radius:50%;background:var(--white)}
.hero .dots .on{width:10px;height:10px;background:var(--gold);margin-left:-1px}

/* services */
.services{position:absolute;left:0;top:1304px;width:1200px;height:635px;background:var(--light)}
.card{position:absolute;top:170px;width:318px;height:383px;border-radius:14px;overflow:hidden}
.card .label{position:absolute;left:12px;right:12px;bottom:16px;height:58px;border-radius:6px;background:var(--white);display:flex;align-items:center;justify-content:center;font-family:"Lato",sans-serif;font-weight:900;font-size:16px;color:var(--ink)}
.card .label.on{background:var(--gold);color:var(--white)}

/* team */
.member{position:absolute;top:2738px;width:170px;text-align:center}
.member .face{width:114px;height:114px;border-radius:50%;margin:0 auto}
.member .n{font-family:"Lato",sans-serif;font-weight:900;font-size:19px;color:var(--ink);margin-top:12px}
.member .r{font-style:italic;font-size:13px;color:#555;margin-top:4px;font-weight:700}

/* cta band */
.cta{position:absolute;left:0;top:3085px;width:1200px;height:315px;background:var(--gold);text-align:center;color:var(--white)}
.cta h3{position:absolute;left:0;right:0;top:68px;font-family:"Outfit",sans-serif;font-weight:700;font-size:50px;letter-spacing:-.5px}
.cta p{position:absolute;left:0;right:0;top:140px;font-size:22px;font-weight:400}
.cta .btn{left:499px;top:184px;width:201px;height:50px;background:transparent;border-color:var(--white);color:var(--white);font-size:14px}

/* footer */
.footer{position:absolute;left:0;top:3400px;width:1200px;height:413px;background:var(--footer);color:var(--white)}
.footer .flogo{position:absolute;left:104px;top:88px;width:254px;color:#e8ecec;font-weight:300;text-align:center}
.footer .flogo .mark{width:20px;height:20px;border:1px solid #e8ecec;margin:0 auto 14px}
.footer .flogo .name{font-size:31px;letter-spacing:1px;line-height:1}
.footer .flogo .sub{font-size:19px;letter-spacing:2px;margin-top:8px}
.footer h4{position:absolute;top:76px;font-family:"Outfit",sans-serif;font-weight:600;font-size:19px}
.footer .links{position:absolute;left:440px;top:118px;font-size:14px;font-weight:700;line-height:31px}
.citem{position:absolute;left:620px;display:flex;gap:12px;align-items:flex-start;font-size:15px;line-height:20px}
.citem .ic{width:38px;height:38px;border-radius:50%;background:var(--gold);flex:none;display:flex;align-items:center;justify-content:center}
.citem b{font-size:13px;font-weight:900;display:block}
.social{position:absolute;top:109px;width:46px;height:46px;border-radius:50%;border:2px solid var(--white);display:flex;align-items:center;justify-content:center}
.social span{width:8px;height:8px;border-radius:50%;background:var(--white)}
</style>
</head>
<body>

<!-- header -->
<div class="topbar">
  <div class="dots"><span></span><span></span><span></span></div>
  <div class="info" style="left:185px">
    <svg width="14" height="14" viewBox="0 0 24 24"><path fill="#fff" d="M6.6 10.8a15.1 15.1 0 0 0 6.6 6.6l2.2-2.2a1 1 0 0 1 1-.25 11.4 11.4 0 0 0 3.6.57 1 1 0 0 1 1 1V20a1 1 0 0 1-1 1A17 17 0 0 1 3 4a1 1 0 0 1 1-1h3.5a1 1 0 0 1 1 1c0 1.25.2 2.45.57 3.57a1 1 0 0 1-.25 1z"/></svg>
    <span><b>FREE CONSULTATION :</b> +1(555) 014-2277</span>
  </div>
  <div class="info" style="left:554px">
    <svg width="17" height="13" viewBox="0 0 24 18"><rect x="1.5" y="1.5" width="21" height="15" rx="2" fill="none" stroke="#fff" stroke-width="2"/><path d="M2 3l10 7 10-7" fill="none" stroke="#fff" stroke-width="2"/></svg>
    <span><b>EMAIL :</b> bramblefordpractice.co.uk</span>
  </div>
</div>

<div class="logo">
  <div class="mark"></div>
  <div class="name">BRAMBLEFORD</div>
  <div class="sub">DENTAL PRACTICE</div>
</div>

<nav class="nav">
  <span class="active">HOME</span><span>ABOUT</span><span>NEW PATIENTS</span><span>TREATMENTS</span><span>FEES</span><span>CONTACT US</span>
</nav>
<div class="btn" style="left:947px;top:56px;width:148px;height:52px;font-size:15px">BOOK ONLINE</div>

<!-- hero -->
<section class="hero" role="img" aria-label="Dentist in white coat and blue gloves treating a smiling patient in the dental chair">
  <div class="dots"><span></span><span class="on"></span><span></span></div>
  <div class="welcome">WELCOME TO</div>
  <div class="big">BRAMBLEFORD</div>
  <div class="sub">DENTAL PRACTICE</div>
  <div class="btn" style="left:104px;top:340px;width:208px;height:51px">GET AN APPOINTMENT</div>
</section>

<!-- about -->
<section>
  <div class="photo" role="img" aria-label="Smiling patient having her teeth checked by gloved hands" style="left:104px;top:776px;width:441px;height:433px;background:linear-gradient(135deg,#e6e4e1,#d2c2b5 50%,#4d8f98 100%)"></div>
  <h2 class="h2 abs" style="left:622px;top:768px;width:500px"><b>ABOUT</b> BRAMBLEFORD DENTAL PRACTICE</h2>
  <div class="rule" style="left:600px;top:864px"></div>
  <p class="para" style="left:622px;top:893px;width:475px;text-align:justify">Welcome to our friendly dental practice nestled in the heart of beautiful Hollowmere, UK. Our team of dedicated dentists, hygienists and support staff are here to provide you with exceptional dental care. With a wide array of services, including general and cosmetic dentistry, orthodontics and emergency care, we’re confident that we can deliver the highest quality treatment to you and your loved ones.At our practice, we believe that a visit to the dentist should be a comfortable and positive experience.</p>
  <div class="btn" style="left:622px;top:1112px;width:125px;height:51px">READ MORE</div>
</section>

<!-- services -->
<section class="services">
  <h2 class="h2 abs" style="left:0;right:0;top:60px;text-align:center"><b>OUR</b> SERVICES</h2>
  <div class="rule" style="left:573px;top:118px"></div>
  <div class="card" role="img" aria-label="Portrait of a smiling woman" style="left:104px;background:linear-gradient(160deg,#c9b7a6,#e7dcd2 60%,#f2efec)"><div class="label">GENERAL AND COSMETIC</div></div>
  <div class="card" role="img" aria-label="Orthodontist examining a patient" style="left:441px;background:linear-gradient(160deg,#dcd9d6,#2b3a4c 55%,#3a3b40)"><div class="label on">ORTHODONTICS</div></div>
  <div class="card" role="img" aria-label="Man holding his cheek with toothache" style="left:780px;background:linear-gradient(160deg,#5a5450,#a38f82 50%,#44505c)"><div class="label">EMERGENCY CARE</div></div>
</section>

<!-- join -->
<section>
  <h2 class="h2 abs" style="left:104px;top:2044px"><b>JOIN</b> OUR PRACTICE</h2>
  <div class="rule" style="left:104px;top:2099px"></div>
  <p class="para" style="left:104px;top:2133px;width:462px">If you’re looking for an exceptional dental practice, we’re here to help! Our team is made up of highly skilled professionals who are dedicated to ensuring that all our patients receive top-notch care in a welcoming and comfortable environment.</p>
  <p class="para" style="left:104px;top:2240px;width:462px">Whether you need a routine examination or a more specialised treatment, we have all the resources to provide you with the best dental care possible. Our practice is always up-to-date with the latest techniques and technologies to make sure that our patients receive the best possible results.</p>
  <div class="btn" style="left:104px;top:2378px;width:125px;height:51px">READ MORE</div>
  <div class="photo" role="img" aria-label="Dental team smiling beside a patient in the chair" style="left:622px;top:2034px;width:475px;height:402px;background:linear-gradient(120deg,#e9eaec,#d8dde3 45%,#7f93d0 80%,#6e86c9)"></div>
</section>

<!-- team -->
<section>
  <div class="photo" role="img" aria-label="Smiling senior dentist in dark scrubs with colleagues behind" style="left:104px;top:2531px;width:473px;height:457px;background:linear-gradient(150deg,#b7b3ae,#6d6a67 45%,#23272b 80%)"></div>
  <h2 class="h2 abs" style="left:636px;top:2530px"><b>OUR</b> TEAM</h2>
  <div class="rule" style="left:636px;top:2585px"></div>
  <p class="para" style="left:636px;top:2618px;width:460px">We are delighted to introduce you to our experienced and compassionate dental team. Our team comprises highly skilled dental professionals who are dedicated to providing you with high-quality dental care services.</p>
  <div class="member" style="left:613px"><div class="face" role="img" aria-label="Dentist portrait" style="background:radial-gradient(circle at 50% 40%,#e8eef3,#3c86c4)"></div><div class="n">EDMUND</div><div class="r">Dentist</div></div>
  <div class="member" style="left:775px"><div class="face" role="img" aria-label="Dentist portrait" style="background:radial-gradient(circle at 50% 40%,#f0ece8,#9eb4c2)"></div><div class="n">ROSALIND</div><div class="r">Dentist</div></div>
  <div class="member" style="left:946px"><div class="face" role="img" aria-label="Dentist portrait" style="background:radial-gradient(circle at 50% 40%,#f3f3f3,#b9bdc2)"></div><div class="n">OLIVER HART</div><div class="r">Dentist</div></div>
  <div class="btn" style="left:641px;top:2939px;width:124px;height:50px">READ MORE</div>
</section>

<!-- cta -->
<section class="cta">
  <h3>YOUR SMILE IS SAFE IN OUR HANDS</h3>
  <p>Discover some of the smile transformations from Brambleford Dental Practice</p>
  <div class="btn">VIEW OUR PORTFOLIO</div>
</section>

<!-- footer -->
<footer class="footer">
  <div class="flogo">
    <div class="mark"></div>
    <div class="name">BRAMBLEFORD</div>
    <div class="sub">DENTAL PRACTICE</div>
  </div>
  <div class="abs" role="img" aria-label="Ravelle ratings badge" style="left:108px;top:272px;width:190px;height:96px;display:flex;align-items:center;gap:14px">
    <div style="width:92px;height:92px;border-radius:50%;background:var(--white)"></div>
    <div style="width:82px;height:36px;border-radius:6px;background:var(--gold)"></div>
  </div>

  <h4 style="left:440px">QUICK LINKS</h4>
  <div class="links">HOME<br>ABOUT<br>NEW PATIENTS<br>TREATMENTS<br>FEES<br>CONTACT US</div>

  <h4 style="left:620px">CONTACT US</h4>
  <div class="citem" style="top:120px"><div class="ic"><svg width="17" height="17" viewBox="0 0 24 24"><path fill="#1d3035" d="M6.6 10.8a15.1 15.1 0 0 0 6.6 6.6l2.2-2.2a1 1 0 0 1 1-.25 11.4 11.4 0 0 0 3.6.57 1 1 0 0 1 1 1V20a1 1 0 0 1-1 1A17 17 0 0 1 3 4a1 1 0 0 1 1-1h3.5a1 1 0 0 1 1 1c0 1.25.2 2.45.57 3.57a1 1 0 0 1-.25 1z"/></svg></div><div><b>PHONE NO :</b>+1(555) 014 2277</div></div>
  <div class="citem" style="top:180px"><div class="ic"><svg width="16" height="20" viewBox="0 0 16 22"><path fill="#1d3035" d="M8 0a8 8 0 0 0-8 8c0 6 8 14 8 14s8-8 8-14a8 8 0 0 0-8-8zm0 11a3 3 0 1 1 0-6 3 3 0 0 1 0 6z"/></svg></div><div><b>LOCATION :</b>Lorem ipsum dolor<br>amet,consectetur,USA</div></div>
  <div class="citem" style="top:258px"><div class="ic"><svg width="17" height="13" viewBox="0 0 24 18"><rect x="1" y="1" width="22" height="16" rx="2" fill="#1d3035"/><path d="M2 3l10 7 10-7" fill="none" stroke="#d9a35e" stroke-width="2"/></svg></div><div><b>EMAIL ADRESS :</b>hello@bramblefordpractice.co.uk</div></div>

  <h4 style="left:913px">FOLLOW US</h4>
  <div class="social" style="left:918px;background:var(--gold);border-color:var(--gold)"><span></span></div>
  <div class="social" style="left:979px"><span></span></div>
  <div class="social" style="left:1040px"><span></span></div>

  <div class="abs" style="left:318px;top:316px;width:774px;height:1px;background:#4b5d62"></div>
  <div class="abs" style="left:318px;top:338px;width:774px;text-align:center;font-size:14px;color:#e8ecec">Copyright © 2025 Brambleford Dental Practice | All Rights Reserved</div>
</footer>

</body>
</html>
```